Webdesign für Personalvermittlung
Zielgruppe
Personalvermittlung
Aufgabenstellung
es soll einladend - nicht zu überladen und natürlich cool und modern sein

```html
<!DOCTYPE html>
<html lang="de">
<head>
<meta charset="utf-8">
<title>Stellenhafen – Bewerber über uns</title>
<link href="https://fonts.googleapis.com/css2?family=Outfit:wght@400;500;600;700;800&display=swap" rel="stylesheet">
<style>
:root{
  --green:#6abd45;
  --green-dark:#3f8a2e;
  --ink:#333333;
  --muted:#555555;
  --white:#ffffff;
  --blue:#2b9fe0;
  --footer:#f6f6f8;
  --line:#444444;
}
*{box-sizing:border-box;margin:0;padding:0}
html,body{width:1200px;height:2311px;overflow:hidden;background:var(--white)}
body{position:relative;font-family:"Outfit",sans-serif;color:var(--ink)}
.abs{position:absolute}
.brand{position:absolute;left:125px;display:flex;flex-direction:column;align-items:center;gap:6px;width:118px}
.brand-dot{width:36px;height:36px;border-radius:50%;background:var(--green)}
.brand-name{font-size:12px;font-weight:700;letter-spacing:.4px;color:#1d2a44}
.nav{position:absolute;right:123px;display:flex;gap:40px;font-size:16px;font-weight:600}
.hero-nav a{color:var(--white);text-decoration:none}
.hero-nav a.active{color:var(--green-dark)}
.hero-title{position:absolute;left:123px;top:140px;width:420px;font-size:44px;line-height:53px;font-weight:700;text-transform:uppercase;color:var(--ink)}
.hero-title em{font-style:normal;color:var(--green)}
.hero-lead{position:absolute;left:123px;top:420px;width:390px;font-size:22px;line-height:28px;font-weight:400;color:var(--ink)}
.photo{position:absolute;border-radius:6px}
.hero-photo{left:531px;top:122px;width:546px;height:395px;background:linear-gradient(120deg,#c9d2dc 0%,#a9b9cc 40%,#6f86a9 65%,#b08a66 100%)}
.testimonials{position:absolute;top:600px;left:123px;display:flex;gap:27px;align-items:flex-start}
.col{display:flex;flex-direction:column;gap:27px;width:300px}
.card{background:var(--white);border-radius:6px;box-shadow:0 2px 10px rgba(0,0,0,.10);padding:17px 10px 13px 14px}
.card-head{display:flex;align-items:flex-start;gap:16px;height:40px;margin-bottom:16px}
.quote{width:46px;height:30px;flex:none;margin-top:1px}
.name{font-size:22px;font-weight:600;line-height:22px}
.role{font-size:16px;font-weight:400;color:var(--muted);line-height:18px}
.card p{font-size:15px;line-height:28px;font-weight:400;color:var(--muted);white-space:nowrap}
.kicker{position:absolute;left:615px;top:1538px;font-size:21px;color:var(--green);font-weight:400}
.contact-title{position:absolute;left:615px;top:1564px;font-size:38px;line-height:40px;font-weight:700;color:var(--ink)}
.group-photo{left:123px;top:1536px;width:463px;height:463px;background:linear-gradient(180deg,#eef0f2 0%,#d7d9dc 40%,#8b8f96 75%,#5d7190 100%)}
.field{position:absolute;background:var(--white);border-radius:15px;height:30px;font-size:15px;color:#b5b5b5;padding:6px 14px;display:flex;align-items:center;justify-content:space-between}
.field.dark{color:var(--ink)}
.field.area{height:169px;align-items:flex-start;border-radius:16px}
.send{position:absolute;left:613px;top:2029px;width:152px;height:32px;border-radius:16px;background:var(--blue);color:var(--white);font-size:16px;font-weight:400;display:flex;align-items:center;justify-content:center;gap:18px}
.footer{position:absolute;left:0;top:2188px;width:1200px;height:123px;background:var(--footer)}
.foot-nav{top:10px;font-weight:400;color:var(--ink)}
.social{position:absolute;right:123px;top:52px;display:flex;gap:22px}
.social span{width:18px;height:18px;border-radius:50%;background:#4a6172}
.rule{position:absolute;left:123px;right:123px;top:86px;border-top:1px solid var(--line)}
.copy{position:absolute;left:123px;top:98px;font-size:14px;color:var(--muted)}
.legal{position:absolute;right:123px;top:98px;font-size:14px;color:var(--muted);display:flex;gap:28px}
</style>
</head>
<body>

<svg class="abs" style="left:0;top:0" width="1200" height="2311" aria-hidden="true">
  <polygon points="558,0 1200,0 1200,474 600,474 622,122" fill="#6abd45"/>
  <polygon points="0,718 404,718 670,1213 0,1213" fill="#6abd45"/>
  <polygon points="586,1668 1200,1668 1200,2073 377,2073 339,1999 586,1999" fill="#6abd45"/>
</svg>

<header>
  <div class="brand" style="top:16px"><span class="brand-dot"></span><span class="brand-name">STELLENHAFEN</span></div>
  <nav class="nav hero-nav" style="top:39px">
    <a>Home</a><a class="active">Bewerber über uns</a><a>Wir über uns</a>
  </nav>
</header>

<h1 class="hero-title"><em>Bewerber</em> haben folgendes bei uns erlebt und schildern ihre <em>Erfahrung</em></h1>
<p class="hero-lead">Erfahrungsberichte und Meinungen unserer Kunden sind für uns von unschätzbarem Wert.</p>
<div class="photo hero-photo" role="img" aria-label="Foto: lächelnde Bewerberin im Vorstellungsgespräch, reicht Lebenslauf über den Tisch"></div>

<section class="testimonials">
  <div class="col">
    <article class="card"><div class="card-head"><svg class="quote" viewBox="0 0 46 30"><path d="M0 30V14Q0 2 12 0v6q-5 2-5 8h5v16zM25 30V14q0-12 12-14v6q-5 2-5 8h5v16z" fill="#3f8a2e"/></svg><div><div class="name">Max Muster</div><div class="role">Leitung Musterbereich</div></div></div><p>Lorem ipsum dolor sit amet,<br>consetetur sadipscing elitr, sed diam<br>nonumy eirmod tempor invidunt ut<br>labore et dolore magna aliquyam erat,<br>sed diam voluptua. At vero eos et<br>accusam et justo duo dolores et ea</p></article>
    <article class="card"><div class="card-head"><svg class="quote" viewBox="0 0 46 30"><path d="M0 30V14Q0 2 12 0v6q-5 2-5 8h5v16zM25 30V14q0-12 12-14v6q-5 2-5 8h5v16z" fill="#3f8a2e"/></svg><div><div class="name">Max Muster</div><div class="role">Leitung Musterbereich</div></div></div><p>Lorem ipsum dolor sit amet,<br>consetetur sadipscing elitr, sed diam<br>nonumy eirmod tempor invidunt ut<br>labore et dolore magna aliquyam erat,<br>sed diam voluptua. At vero eos et<br>accusam et justo duo dolores et ea<br>rebum. Stet clita kasd gubergren, no<br>sea takimata sanctus est Lorem<br>ipsum dolor sit amet.</p></article>
    <article class="card"><div class="card-head"><svg class="quote" viewBox="0 0 46 30"><path d="M0 30V14Q0 2 12 0v6q-5 2-5 8h5v16zM25 30V14q0-12 12-14v6q-5 2-5 8h5v16z" fill="#3f8a2e"/></svg><div><div class="name">Max Muster</div><div class="role">Leitung Musterbereich</div></div></div><p>Lorem ipsum dolor sit amet,<br>consetetur sadipscing elitr, sed diam<br>nonumy eirmod tempor invidunt ut<br>labore et dolore magna aliquyam erat,</p></article>
  </div>
  <div class="col">
    <article class="card"><div class="card-head"><svg class="quote" viewBox="0 0 46 30"><path d="M0 30V14Q0 2 12 0v6q-5 2-5 8h5v16zM25 30V14q0-12 12-14v6q-5 2-5 8h5v16z" fill="#3f8a2e"/></svg><div><div class="name">Max Muster</div><div class="role">Leitung Musterbereich</div></div></div><p>Lorem ipsum dolor sit amet,<br>consetetur sadipscing elitr, sed diam<br>nonumy eirmod tempor invidunt ut<br>labore et dolore magna aliquyam erat,<br>sed diam voluptua. At vero eos et<br>accusam et justo duo dolores et ea<br>rebum. Stet clita kasd gubergren, no<br>sea takimata sanctus est Lorem<br>ipsum dolor sit amet.</p></article>
    <article class="card"><div class="card-head"><svg class="quote" viewBox="0 0 46 30"><path d="M0 30V14Q0 2 12 0v6q-5 2-5 8h5v16zM25 30V14q0-12 12-14v6q-5 2-5 8h5v16z" fill="#3f8a2e"/></svg><div><div class="name">Max Muster</div><div class="role">Leitung Musterbereich</div></div></div><p>Lorem ipsum dolor sit amet,<br>consetetur sadipscing elitr, sed diam<br>nonumy eirmod tempor invidunt ut<br>labore et dolore magna aliquyam erat,</p></article>
    <article class="card"><div class="card-head"><svg class="quote" viewBox="0 0 46 30"><path d="M0 30V14Q0 2 12 0v6q-5 2-5 8h5v16zM25 30V14q0-12 12-14v6q-5 2-5 8h5v16z" fill="#3f8a2e"/></svg><div><div class="name">Max Muster</div><div class="role">Leitung Musterbereich</div></div></div><p>Lorem ipsum dolor sit amet,<br>consetetur sadipscing elitr, sed diam<br>nonumy eirmod tempor invidunt ut<br>labore et dolore magna aliquyam erat,<br>sed diam voluptua. At vero eos et<br>accusam et justo duo dolores et ea</p></article>
  </div>
  <div class="col">
    <article class="card"><div class="card-head"><svg class="quote" viewBox="0 0 46 30"><path d="M0 30V14Q0 2 12 0v6q-5 2-5 8h5v16zM25 30V14q0-12 12-14v6q-5 2-5 8h5v16z" fill="#3f8a2e"/></svg><div><div class="name">Max Muster</div><div class="role">Leitung Musterbereich</div></div></div><p>Lorem ipsum dolor sit amet,<br>consetetur sadipscing elitr, sed diam<br>nonumy eirmod tempor invidunt ut<br>labore et dolore magna aliquyam erat,</p></article>
    <article class="card"><div class="card-head"><svg class="quote" viewBox="0 0 46 30"><path d="M0 30V14Q0 2 12 0v6q-5 2-5 8h5v16zM25 30V14q0-12 12-14v6q-5 2-5 8h5v16z" fill="#3f8a2e"/></svg><div><div class="name">Max Muster</div><div class="role">Leitung Musterbereich</div></div></div><p>Lorem ipsum dolor sit amet,<br>consetetur sadipscing elitr, sed diam<br>nonumy eirmod tempor invidunt ut<br>labore et dolore magna aliquyam erat,<br>sed diam voluptua. At vero eos et<br>accusam et justo duo dolores et ea</p></article>
    <article class="card"><div class="card-head"><svg class="quote" viewBox="0 0 46 30"><path d="M0 30V14Q0 2 12 0v6q-5 2-5 8h5v16zM25 30V14q0-12 12-14v6q-5 2-5 8h5v16z" fill="#3f8a2e"/></svg><div><div class="name">Max Muster</div><div class="role">Leitung Musterbereich</div></div></div><p>Lorem ipsum dolor sit amet,<br>consetetur sadipscing elitr, sed diam<br>nonumy eirmod tempor invidunt ut<br>labore et dolore magna aliquyam erat,<br>sed diam voluptua. At vero eos et<br>accusam et justo duo dolores et ea<br>rebum. Stet clita kasd gubergren, no<br>sea takimata sanctus est Lorem<br>ipsum dolor sit amet.</p></article>
  </div>
</section>

<section class="contact">
  <div class="photo group-photo" role="img" aria-label="Foto: fröhliche Gruppe junger Menschen in einem hellen Raum"></div>
  <div class="kicker">KONTAKT</div>
  <h2 class="contact-title">WIR FREUEN UNS AUF<br>DICH</h2>
  <div class="field" style="left:613px;top:1692px;width:218px">Vorname*</div>
  <div class="field" style="left:858px;top:1692px;width:219px">Nachname*</div>
  <div class="field" style="left:613px;top:1738px;width:464px">E-Mail*</div>
  <div class="field dark" style="left:613px;top:1789px;width:218px">Rückruf erwünscht?
    <svg width="20" height="12" viewBox="0 0 20 12"><path d="M1 1l9 9 9-9" fill="none" stroke="#333" stroke-width="2.2"/></svg></div>
  <div class="field dark" style="left:858px;top:1789px;width:219px">Lebenslauf hochladen
    <svg width="18" height="18" viewBox="0 0 18 18" fill="none" stroke="#333" stroke-width="1.6"><circle cx="2" cy="3" r="1"/><circle cx="2" cy="9" r="1"/><circle cx="2" cy="15" r="1"/><rect x="6" y="1" width="11" height="4" rx="2"/><rect x="6" y="7" width="11" height="4" rx="2"/><rect x="6" y="13" width="11" height="4" rx="2"/></svg></div>
  <div class="field area" style="left:613px;top:1840px;width:464px">Nachricht</div>
  <div class="send">Absenden
    <svg width="22" height="16" viewBox="0 0 22 16" fill="none" stroke="#fff" stroke-width="1.8"><rect x="1" y="1" width="20" height="14" rx="3"/><path d="M2 3l9 6 9-6"/></svg></div>
</section>

<footer class="footer">
  <div class="brand" style="top:11px"><span class="brand-dot"></span><span class="brand-name">STELLENHAFEN</span></div>
  <nav class="nav foot-nav"><a>Home</a><a>Bewerber über uns</a><a>Wir über uns</a></nav>
  <div class="social"><span></span><span></span></div>
  <div class="rule"></div>
  <div class="copy">© 2024 kolibri-atelier.de</div>
  <div class="legal"><span>Impressum</span><span>Datenschutz</span></div>
</footer>

</body>
</html>
```